New Business Card Design Project

We require a business card design for Vexalund, a newly established Indian company.
Our focus is on the development, manufacturing, and export of a diverse array of pharmaceutical products on a global scale. The card should convey a professional appearance, as our primary markets are in Africa, China, and Southeast Asian nations.
We envision a two-sided business card, with the reverse side dedicated to a logo set against a solid color or an elegantly designed pattern. The corners should be rounded. We would appreciate seeing both horizontal and vertical design options. We trust the designer to utilize their expertise in creating this design.

The content for the business card is included in the attached Word file.

Target Market(s)

Our primary markets are in Africa, China, and Southeast Asian, Latin America, Maldives, Sri Lanka

Industry/Entity Type

Pharmaceutical Manufacturing and Export

Contact Information for Business Card

Colors

Designer to choose colors to be used in the design.

Requirements
Must have
• The reverse side of the business card features solely the logo along with the tagline, "Remedies of Life."
Should not have
• The logo should not exceed two instances, encompassing both the front and back sides of the card.

```html
<!DOCTYPE html>
<html lang="en">
<head>
<meta charset="utf-8">
<title>Vexalund Business Card</title>
<link href="https://fonts.googleapis.com/css2?family=Poppins:wght@400;500;600;700&display=swap" rel="stylesheet">
<style>
  :root {
    --bg: #121212;
    --card-white: #ffffff;
    --brand-blue: #1b96d9;
    --brand-blue-deep: #1a86c4;
    --brand-red: #ea4c3c;
    --ink: #2e2e2e;
    --soft-blue: #e3f1fa;
    --soft-red: #fde8e6;
  }
  * { margin: 0; padding: 0; box-sizing: border-box; }
  html, body {
    width: 1200px; height: 1059px; overflow: hidden;
    background: var(--bg);
    font-family: "Poppins", sans-serif;
  }
  .stage { position: relative; width: 1200px; height: 1059px; }
  .card {
    position: absolute; top: 182px;
    width: 393px; height: 692px;
    border-radius: 20px; overflow: hidden;
  }
  .card--front { left: 177px; background: var(--card-white); }
  .card--back {
    left: 646px;
    background: linear-gradient(180deg, #2ba2e2 0%, var(--brand-blue) 45%, var(--brand-blue-deep) 100%);
  }
  .soft-decoration {
    position: absolute; left: 0; bottom: 0; width: 100%; height: 290px;
    background: linear-gradient(90deg, var(--soft-blue) 0%, var(--soft-blue) 42%, var(--soft-red) 58%, rgba(253,232,230,0.4) 100%);
    -webkit-mask-image: linear-gradient(180deg, transparent 0%, #000 40%);
    mask-image: linear-gradient(180deg, transparent 0%, #000 40%);
    opacity: .75;
  }
  .brand-dot {
    position: absolute; left: 50%; width: 56px; height: 56px;
    margin-left: -28px; border-radius: 50%;
  }
  .card--front .brand-dot { top: 105px; background: var(--brand-blue); }
  .card--back .brand-dot { top: 285px; background: #ffffff; }
  .brand-name {
    position: absolute; left: 0; width: 100%; text-align: center;
    font-weight: 600; line-height: 1;
  }
  .card--front .brand-name { top: 214px; font-size: 52px; color: var(--brand-blue); }
  .card--back .brand-name { top: 394px; font-size: 62px; color: #ffffff; }
  .tagline {
    position: absolute; left: 0; width: 100%; top: 474px; text-align: center;
    font-size: 17px; font-weight: 500; letter-spacing: 3px; color: #ffffff;
  }
  .details {
    position: absolute; right: 38px; top: 352px;
    text-align: right; color: var(--ink); font-size: 16px;
  }
  .person-name { font-size: 25px; font-weight: 700; line-height: 1.2; }
  .person-name .first { color: var(--brand-blue); }
  .person-name .last { color: var(--brand-red); }
  .role { font-size: 16px; line-height: 1.3; }
  .divider {
    display: block; width: 12px; height: 1.5px; background: var(--brand-blue);
    margin: 16px 0 12px auto;
  }
  .address { font-size: 16px; line-height: 1.45; }
  .contact-list { list-style: none; font-size: 16.5px; line-height: 1.68; }
  .contact-list li { display: flex; justify-content: flex-end; align-items: center; gap: 10px; }
  .contact-list svg { width: 12px; height: 12px; fill: var(--brand-red); flex: none; }
</style>
</head>
<body>
<div class="stage">
  <section class="card card--front">
    <div class="soft-decoration" role="img" aria-label="Faint brand symbol in pale blue and pale red"></div>
    <span class="brand-dot"></span>
    <h1 class="brand-name">Vexalund</h1>
    <div class="details">
      <p class="person-name"><span class="first">Ravi K.</span> <span class="last">Solanke</span></p>
      <p class="role">CEO<br>Vexalund</p>
      <span class="divider"></span>
      <p class="address">Plot No.14, Sunmesh Colony<br>Kesar Road, Dhamangaon<br>Pin Code: 444709, Maharashtra, India</p>
      <span class="divider"></span>
      <ul class="contact-list">
        <li>+919876503412
          <svg viewBox="0 0 12 12"><path d="M1 4c0-2 2-3 5-3s5 1 5 3v1H8V4H4v1H1zM2 6h8l1 5H1z"/></svg></li>
        <li>rsolanke@vexalund.com
          <svg viewBox="0 0 12 12"><path d="M1 3h10v7H1zM1 3l5 4 5-4"/></svg></li>
        <li>www.vexalund.com
          <svg viewBox="0 0 12 12"><circle cx="6" cy="6" r="5.5"/></svg></li>
      </ul>
    </div>
  </section>

  <section class="card card--back" role="img" aria-label="Blue background with a repeating faint brand pattern">
    <span class="brand-dot"></span>
    <h2 class="brand-name">Vexalund</h2>
    <p class="tagline">Remedies of Life</p>
  </section>
</div>
</body>
</html>
```